VitaBraid Web Design. Health and Wellness Industry

We are in process of creating next big Cloud based Health Care Management system. We have created 1st draft of Landing Page design. It is missing curb appeal, jazzy feel and engaging modern look.

Need a talented designer to recreate UI/ UX and take it to the next level.
If you are a creative designer, gifted with vision and imagination, I strongly encourage you to participate.

I want the designers to stay focus on the Landing page
Once we select the winner we will provide other subsequent pages
Follow up pages will be similar simple design

Target Market(s)

Individual Users and small business
Age Group 35-75
Individuals involved in "Health and Fitness" activity tracking, managing etc.

Industry/Entity Type

Health And Wellness

Number of Pages Required

5+ page

Colors
f68e4e
34a6d7

Requirements
Must have
• Super Engaging UI/ UX
• Smart and Contemporary look
• Easy to Navigate
• Folder Style menu bar
• Slideshow
• Social Medial Friendly
• Online Shopping
Nice to have
• Start from the enclosed draft Landing Page Idea.
• Feel Free to include additional frame, information section, Icon etc.

```html
<!DOCTYPE html>
<html lang="en">
<head>
<meta charset="utf-8">
<title>VitaBraid – Health Management Landing Page</title>
<link href="https://fonts.googleapis.com/css2?family=Open+Sans:wght@300;400;600;700&display=swap" rel="stylesheet">
<style>
  :root{
    --orange:#f68e4e;
    --orange-deep:#ef7a30;
    --blue:#34a6d7;
    --ink:#333333;
    --muted:#8a8a8a;
    --line:#e2e2e2;
    --soft:#f2f2f2;
    --footer:#2b2b2b;
    --footer-bar:#1f1f1f;
    --white:#ffffff;
  }
  *{box-sizing:border-box;margin:0;padding:0}
  html,body{width:1200px;height:2568px;overflow:hidden}
  body{font-family:"Open Sans",Arial,sans-serif;color:var(--ink);background:var(--white);font-size:13px;line-height:1.6}
  .wrap{width:1000px;margin:0 auto;position:relative}

  /* header */
  .site-header{height:72px;border-bottom:1px solid var(--line);background:var(--white)}
  .site-header .wrap{height:72px;display:flex;align-items:center}
  .brand{display:flex;align-items:center;gap:10px}
  .brand-mark{width:30px;height:30px;border-radius:50%;background:var(--orange)}
  .brand-name{font-size:30px;font-weight:700;color:var(--orange);line-height:1}
  .brand-tag{font-size:9px;color:var(--muted);display:block;margin-top:3px;letter-spacing:.5px}
  .main-nav{display:flex;margin-left:110px;height:72px}
  .main-nav a{display:flex;align-items:center;padding:0 26px;color:var(--ink);text-decoration:none;font-size:14px;border-left:1px solid var(--line)}
  .main-nav a:last-child{border-right:1px solid var(--line)}
  .main-nav a.active{color:var(--orange);border-top:3px solid var(--orange)}
  .account-links{position:absolute;right:0;top:10px;font-size:10px;color:var(--muted);display:flex;gap:14px}
  .account-links span::before{content:"";display:inline-block;width:7px;height:7px;border-radius:50%;background:var(--orange);margin-right:4px}

  /* hero */
  .hero{height:470px;position:relative;background:linear-gradient(100deg,#f6f7f8 0%,#e9ecef 45%,#dfe3e6 100%)}
  .hero-visual{position:absolute;left:0;top:0;width:760px;height:470px;background:linear-gradient(110deg,#eef0f2 0%,#d7dce0 40%,#c8ced3 60%,#e8ebed 100%)}
  .hero-copy{position:absolute;right:100px;top:80px;text-align:right}
  .hero-copy .sub{font-size:30px;font-weight:300;color:#555}
  .hero-copy .main{font-size:40px;font-weight:600;color:var(--orange);line-height:1.1}
  .hero-dots{position:absolute;right:100px;bottom:20px;display:flex;gap:6px}
  .hero-dots i{width:16px;height:4px;background:#b8b8b8;display:block}
  .hero-dots i.on{background:var(--orange)}

  /* welcome */
  .welcome{height:330px;background:var(--orange);color:var(--white)}
  .welcome .wrap{display:flex;gap:40px;padding-top:34px}
  .welcome-text{width:660px}
  .welcome h1{font-size:34px;font-weight:400;margin-bottom:12px}
  .welcome h1 b{font-weight:700}
  .welcome p{font-size:12.5px;margin-bottom:14px;opacity:.95}
  .btn-dark{display:inline-block;background:#5a3a26;color:var(--white);font-size:11px;padding:7px 18px;text-transform:uppercase}
  .welcome-photo{width:300px;height:260px;background:linear-gradient(135deg,#dfe9f0,#9fb8c9 60%,#6f8ea3)}

  /* features */
  .features{padding:44px 0 30px;height:340px}
  .features .wrap{display:flex;justify-content:space-between}
  .feature{width:230px;text-align:center}
  .feature-icon{width:66px;height:66px;border-radius:50%;border:2px solid var(--orange);margin:0 auto 14px;display:flex;align-items:center;justify-content:center}
  .feature h3{font-size:16px;font-weight:400;margin-bottom:8px}
  .feature p{font-size:11.5px;color:var(--muted);margin-bottom:10px}
  .more{font-size:10px;font-weight:700;text-transform:uppercase;color:var(--ink)}
  .more::after{content:" \25B6";font-size:8px}

  /* products */
  .products{height:540px}
  .section-title{text-align:center;font-size:32px;font-weight:300;color:#555;position:relative;padding-bottom:14px}
  .section-title b{font-weight:600;color:var(--ink)}
  .section-title::after{content:"";position:absolute;left:50%;bottom:0;width:60px;height:2px;margin-left:-30px;background:var(--orange)}
  .product-row{display:flex;justify-content:space-between;margin-top:28px}
  .product{width:226px}
  .product-photo{height:210px;border:1px solid var(--line);display:flex;align-items:center;justify-content:center}
  .product-photo span{display:block;width:120px;height:170px}
  .product h4{font-size:12.5px;font-weight:600;margin:14px 0 6px}
  .product p{font-size:11.5px;color:var(--muted);margin-bottom:12px}
  .btn-outline{display:inline-block;border:1px solid var(--orange);color:var(--orange);font-size:10px;padding:4px 12px;text-transform:uppercase}

  /* testimonials */
  .testimonials{height:310px;background:linear-gradient(180deg,#ececec,#e0e0e0);padding-top:30px;position:relative}
  .testimonials .section-title{color:#666}
  .quote{width:720px;margin:24px auto 0;text-align:center;font-size:12.5px;color:#666}
  .signature{width:230px;height:22px;margin:18px auto 0;background:linear-gradient(90deg,transparent,#cfa98a,transparent)}
  .arrow{position:absolute;top:140px}
  .arrow.prev{left:100px}.arrow.next{right:100px}

  /* partners */
  .partners{height:140px;display:flex;align-items:center}
  .partners .wrap{display:flex;align-items:center;justify-content:space-between}
  .partner{width:150px;height:64px;background:#e6e6e6;border-radius:4px}
  .partner.round{width:70px;height:64px;border-radius:6px}

  /* footer */
  .site-footer{height:290px;background:var(--footer);color:#bdbdbd;padding-top:34px}
  .site-footer .wrap{display:flex;justify-content:space-between}
  .f-col{width:170px}
  .f-col.news{width:210px}
  .f-col h5{color:var(--white);font-size:13px;font-weight:600;margin-bottom:14px}
  .f-col h6{color:var(--white);font-size:12px;font-weight:600}
  .f-col .date{font-size:10px;color:#8d8d8d;margin-bottom:6px}
  .f-col p{font-size:11px}
  .f-col ul{list-style:none}
  .f-col li{font-size:11px;line-height:1.9}
  .f-col li::before{content:"\25A0";font-size:6px;color:var(--orange);margin-right:7px;vertical-align:middle}
  .footer-bar{height:58px;background:var(--footer-bar)}
  .footer-bar .wrap{height:58px;display:flex;align-items:center;justify-content:space-between;font-size:10px;color:#8d8d8d}
  .social{display:flex;gap:8px}
  .social i{width:24px;height:24px;border-radius:50%;background:#d9d9d9;display:block}
</style>
</head>
<body>

<header class="site-header">
  <div class="wrap">
    <div class="brand">
      <span class="brand-mark"></span>
      <div>
        <span class="brand-name">VitaBraid</span>
        <span class="brand-tag">health management help tool</span>
      </div>
    </div>
    <nav class="main-nav">
      <a class="active">Home</a>
      <a>Discover VitaBraid</a>
      <a>Shop</a>
      <a>Caregiver</a>
      <a>Contacts</a>
    </nav>
    <div class="account-links"><span>Login</span><span>Register</span></div>
  </div>
</header>

<section class="hero">
  <div class="hero-visual" role="img" aria-label="Doctor's hand holding a stethoscope beside a grid of hexagonal health icons"></div>
  <div class="hero-copy">
    <div class="sub">Organize Your</div>
    <div class="main">Health Information</div>
  </div>
  <div class="hero-dots"><i class="on"></i><i></i><i></i></div>
</section>

<section class="welcome">
  <div class="wrap">
    <div class="welcome-text">
      <h1>Welcome to <b>VitaBraid</b></h1>
      <p>VitaBraid brings your records, medications, appointments and daily fitness data together in one secure cloud space. Track progress, share results with your doctor and keep your family informed from any device, at any time. Our tools are simple to learn and built for people who want clear answers about their health without extra effort.</p>
      <p>Start with a free profile, invite a caregiver and connect your favourite trackers. Every update is stored safely and shown in easy charts, so you always know where you stand and what to do next.</p>
      <span class="btn-dark">Read More</span>
    </div>
    <div class="welcome-photo" role="img" aria-label="Collage of doctors reviewing patient data on screens"></div>
  </div>
</section>

<section class="features">
  <div class="wrap">
    <div class="feature">
      <div class="feature-icon"><svg width="30" height="30" viewBox="0 0 30 30"><path d="M3 15c4-6 8-8 12-8s8 2 12 8c-4 6-8 8-12 8s-8-2-12-8z" fill="none" stroke="#f68e4e" stroke-width="2"/><circle cx="15" cy="15" r="4" fill="#f68e4e"/></svg></div>
      <h3>Over View</h3>
      <p>Get a clear picture of your records, visits and trends on one calm and simple dashboard.</p>
      <span class="more">Read More</span>
    </div>
    <div class="feature">
      <div class="feature-icon"><svg width="30" height="30" viewBox="0 0 30 30"><circle cx="15" cy="15" r="6" fill="none" stroke="#f68e4e" stroke-width="2"/><path d="M15 3v5M15 22v5M3 15h5M22 15h5M6.5 6.5l3.5 3.5M20 20l3.5 3.5M6.5 23.5l3.5-3.5M20 10l3.5-3.5" stroke="#f68e4e" stroke-width="2"/></svg></div>
      <h3>How It Works</h3>
      <p>Connect devices, add your data and let smart reminders guide each step of your routine.</p>
      <span class="more">Read More</span>
    </div>
    <div class="feature">
      <div class="feature-icon"><svg width="30" height="30" viewBox="0 0 30 30"><path d="M4 6h22v14H12l-6 5v-5H4z" fill="none" stroke="#f68e4e" stroke-width="2" stroke-linejoin="round"/></svg></div>
      <h3>Stories</h3>
      <p>Read how members and caregivers use the platform to reach goals and stay well together.</p>
      <span class="more">Read More</span>
    </div>
    <div class="feature">
      <div class="feature-icon"><svg width="30" height="30" viewBox="0 0 30 30"><path d="M6 15h16M16 8l7 7-7 7" fill="none" stroke="#f68e4e" stroke-width="2.4" stroke-linecap="round" stroke-linejoin="round"/></svg></div>
      <h3>Get Started</h3>
      <p>Create your free account in minutes and begin organizing your health information today.</p>
      <span class="more">Read More</span>
    </div>
  </div>
</section>

<section class="products">
  <div class="wrap">
    <h2 class="section-title">Featured <b>Products</b></h2>
    <div class="product-row">
      <div class="product">
        <div class="product-photo"><span role="img" aria-label="White handheld health monitor" style="background:linear-gradient(180deg,#f4f6f8,#cfd6dc)"></span></div>
        <h4>Smart Pulse Monitor Kit</h4>
        <p>Compact reader for daily pulse checks with fast syncing to your profile.</p>
        <span class="btn-outline">Add to Cart</span>
      </div>
      <div class="product">
        <div class="product-photo"><span role="img" aria-label="White and blue tabletop device" style="background:linear-gradient(180deg,#eef2f5,#8fb8cf)"></span></div>
        <h4>Home Care Air Unit</h4>
        <p>Quiet tabletop unit that keeps rooms fresh for better rest and recovery.</p>
        <span class="btn-outline">Add to Cart</span>
      </div>
      <div class="product">
        <div class="product-photo"><span role="img" aria-label="Black square digital body scale" style="width:170px;height:150px;background:linear-gradient(135deg,#3a3a3a,#111)"></span></div>
        <h4>Digital Body Scale</h4>
        <p>Tracks weight and body trends, then sends results straight to your charts.</p>
        <span class="btn-outline">Add to Cart</span>
      </div>
      <div class="product">
        <div class="product-photo"><span role="img" aria-label="Black fitness tracker wristband" style="width:150px;height:150px;border-radius:50%;background:radial-gradient(circle,#4a4a4a,#151515)"></span></div>
        <h4>Activity Tracker Band</h4>
        <p>Counts steps, sleep and heart rate all day with a long lasting battery.</p>
        <span class="btn-outline">Add to Cart</span>
      </div>
    </div>
  </div>
</section>

<section class="testimonials">
  <h2 class="section-title">Client <b>Testimonials</b></h2>
  <p class="quote">Since we started using this service our whole family keeps its medical notes in one place. Appointments are easier, our doctor sees the full picture, and we finally feel in control of our health instead of chasing paperwork every single week.</p>
  <div class="signature" role="img" aria-label="Handwritten client signature"></div>
  <svg class="arrow prev" width="14" height="22" viewBox="0 0 14 22"><path d="M11 2L3 11l8 9" fill="none" stroke="#444" stroke-width="3"/></svg>
  <svg class="arrow next" width="14" height="22" viewBox="0 0 14 22"><path d="M3 2l8 9-8 9" fill="none" stroke="#444" stroke-width="3"/></svg>
</section>

<section class="partners">
  <div class="wrap">
    <svg width="12" height="20" viewBox="0 0 12 20"><path d="M10 2L3 10l7 8" fill="none" stroke="#444" stroke-width="2.5"/></svg>
    <span class="partner round"></span>
    <span class="partner"></span>
    <span class="partner"></span>
    <span class="partner"></span>
    <span class="partner"></span>
    <svg width="12" height="20" viewBox="0 0 12 20"><path d="M2 2l7 8-7 8" fill="none" stroke="#444" stroke-width="2.5"/></svg>
  </div>
</section>

<footer class="site-footer">
  <div class="wrap">
    <div class="f-col news">
      <h5>Latest News</h5>
      <h6>Post Title</h6>
      <div class="date">Tuesday, 14 July 2015</div>
      <p>New caregiver sharing tools are now live, letting families view updates, notes and reminders together in real time.</p>
    </div>
    <div class="f-col">
      <h5>Company</h5>
      <ul><li>Home</li><li>About Us</li><li>Our Team</li><li>Careers</li><li>Press</li><li>Contact</li></ul>
    </div>
    <div class="f-col">
      <h5>Products</h5>
      <ul><li>Monitors</li><li>Scales</li><li>Trackers</li><li>Home Care</li><li>Accessories</li><li>Gift Cards</li></ul>
    </div>
    <div class="f-col">
      <h5>Downloads</h5>
      <ul><li>User Guide</li><li>Mobile App</li><li>Desktop App</li><li>Brochure</li><li>Privacy Policy</li></ul>
    </div>
    <div class="f-col">
      <h5>Contacts</h5>
      <ul><li>Support Desk</li><li>Sales Team</li><li>Partners</li><li>Media</li><li>Feedback</li></ul>
    </div>
  </div>
</footer>
<div class="footer-bar">
  <div class="wrap">
    <span>© VitaBraid 2015 | All Rights Reserved</span>
    <div class="social"><i></i><i></i><i></i><i></i></div>
  </div>
</div>

</body>
</html>
```